New Business Card Design Project

We require a business card design for Vexalund, a newly established Indian company.
Our focus is on the development, manufacturing, and export of a diverse array of pharmaceutical products on a global scale. The card should convey a professional appearance, as our primary markets are in Africa, China, and Southeast Asian nations.
We envision a two-sided business card, with the reverse side dedicated to a logo set against a solid color or an elegantly designed pattern. The corners should be rounded. We would appreciate seeing both horizontal and vertical design options. We trust the designer to utilize their expertise in creating this design.

The content for the business card is included in the attached Word file.

Target Market(s)

Our primary markets are in Africa, China, and Southeast Asian, Latin America, Maldives, Sri Lanka

Industry/Entity Type

Pharmaceutical Manufacturing and Export

Contact Information for Business Card

Colors

Designer to choose colors to be used in the design.

Requirements
Must have
• The reverse side of the business card features solely the logo along with the tagline, "Care for Every Day."
Should not have
• The logo should not exceed two instances, encompassing both the front and back sides of the card.

```html
<!DOCTYPE html>
<html lang="en">
<head>
<meta charset="utf-8">
<title>Vexalund Business Card</title>
<link rel="stylesheet" href="https://fonts.googleapis.com/css2?family=Poppins:wght@400;600&family=Great+Vibes&display=swap">
<style>
  :root {
    --stage: #2a2a2a;
    --blue: #2ea8de;
    --mid: #8c8a9c;
    --coral: #c9706a;
    --brand-blue: #25a9e1;
    --brand-coral: #ef614f;
    --white: #ffffff;
    --ink: #1a1a1a;
  }
  * { margin: 0; padding: 0; box-sizing: border-box; }
  html, body {
    width: 1093px; height: 1200px; overflow: hidden;
    background: var(--stage);
    font-family: "Poppins", sans-serif;
  }
  .card {
    position: absolute;
    left: 265px;
    width: 578px;
    height: 356px;
    border-radius: 26px;
    overflow: hidden;
    box-shadow: 0 4px 10px rgba(0,0,0,0.55);
  }
  .card-front {
    top: 226px;
    background: linear-gradient(to top right, var(--blue) 0%, var(--mid) 58%, var(--coral) 100%);
    color: var(--white);
  }
  .card-back {
    top: 621px;
    background: var(--white);
  }
  .holder { position: absolute; left: 26px; top: 38px; line-height: 1.2; }
  .holder-name { font-weight: 600; font-size: 24px; }
  .holder-role, .holder-company { font-size: 17px; font-weight: 400; }
  .brand-name {
    position: absolute; right: 24px; top: 146px;
    font-weight: 600; font-size: 52px; line-height: 1; letter-spacing: 0.5px;
  }
  .contact-list { position: absolute; left: 26px; top: 259px; list-style: none; }
  .contact-list li {
    display: flex; align-items: center; gap: 9px;
    font-size: 18px; line-height: 21px;
  }
  .contact-list svg { width: 16px; height: 16px; flex: none; }
  .address {
    position: absolute; right: 25px; top: 280px;
    text-align: right; font-size: 18px; line-height: 21px;
  }
  .back-brand {
    position: absolute; left: 0; right: 0; top: 118px;
    display: flex; justify-content: center; align-items: center; gap: 14px;
  }
  .back-brand-dot { width: 28px; height: 28px; border-radius: 50%; background: var(--brand-coral); }
  .back-brand-name {
    font-weight: 600; font-size: 54px; line-height: 1; color: var(--brand-blue);
  }
  .tagline {
    position: absolute; left: 0; right: 0; top: 283px;
    text-align: center; font-family: "Great Vibes", cursive;
    font-size: 34px; color: var(--ink);
  }
</style>
</head>
<body>
  <section class="card card-front">
    <div class="holder">
      <p class="holder-name">Rohan K. Sathe</p>
      <p class="holder-role">CEO</p>
      <p class="holder-company">Vexalund</p>
    </div>
    <p class="brand-name">Vexalund</p>
    <ul class="contact-list">
      <li>
        <svg viewBox="0 0 24 24" fill="none" stroke="currentColor" stroke-width="2.2" stroke-linecap="round"><path d="M5 3h4l2 5-2.5 1.5a11 11 0 0 0 6 6L16 13l5 2v4a2 2 0 0 1-2 2A17 17 0 0 1 3 5a2 2 0 0 1 2-2z"/><path d="M14 3a7 7 0 0 1 7 7M14 7a3 3 0 0 1 3 3"/></svg>
        <span>+919000012345</span>
      </li>
      <li>
        <svg viewBox="0 0 24 24" fill="currentColor"><path d="M2 5h20v14H2z"/><path d="M2 5l10 8 10-8" fill="none" stroke="#7f93ad" stroke-width="1.6"/></svg>
        <span>rsathe@vexalund.com</span>
      </li>
      <li>
        <svg viewBox="0 0 24 24" fill="none" stroke="currentColor" stroke-width="2"><circle cx="12" cy="12" r="10"/><path d="M2 12h20M12 2c3 3 3 17 0 20M12 2c-3 3-3 17 0 20M4 7h16M4 17h16"/></svg>
        <span>https://vexalund.com/</span>
      </li>
    </ul>
    <p class="address">12, Sunmarg Colony<br>Kesarpur, 440001, India</p>
  </section>

  <section class="card card-back">
    <div class="back-brand">
      <span class="back-brand-dot"></span>
      <span class="back-brand-name">Vexalund</span>
    </div>
    <p class="tagline">Care for Every Day.</p>
  </section>
</body>
</html>
```